Logo, Web and Mobile Designs for enterprise social media platform

All the details are in the attached document, please start reading the scope document first which explains what is this project about and the details about the needed deliverables, after that please read the UI_Requirements document which will detail what is expected regarding the coded web version since this is a coded contest, it is very important that you meet the UI requirements or suggest something else but we will need to agree first before working on the coded version

Good Luck

Target Market(s)

Enterprise Social Media

Industry/Entity Type

Media

Coding

Coded - Design and coding required

Number of Pages Required

5+ page

Font styles to use
Sans Serif

Requirements
Must have
• All the must haves are listed in the scope document so please check before you start

```html
<!DOCTYPE html>
<html lang="en">
<head>
<meta charset="utf-8">
<title>Teamora – Enterprise Social Platform</title>
<link href="https://fonts.googleapis.com/css2?family=Oswald:wght@500&family=Roboto:wght@400;500;700&display=swap" rel="stylesheet">
<style>
:root{
  --page:#ececec;
  --white:#ffffff;
  --ink:#3a3a3a;
  --muted:#7a7a7a;
  --accent:#2a9fc0;
  --accent-dark:#1f6f98;
  --link:#36479a;
  --orange:#f58a1f;
  --panel-head:#dde5f2;
  --line:#e2e2e2;
  --footer:#e9eef1;
  --footer-bar:#232323;
}
*{box-sizing:border-box;margin:0;padding:0}
html,body{width:1200px;height:2473px;overflow:hidden}
body{background:var(--page);font-family:"Roboto",Arial,sans-serif;color:var(--ink);position:relative}
a{color:inherit;text-decoration:none}

.site-header{position:absolute;left:0;top:0;width:1200px;height:102px;background:linear-gradient(#ffffff,#f3f3f3);border-bottom:1px solid #dcdcdc}
.brand{position:absolute;left:90px;top:36px;display:flex;align-items:center;gap:12px;font-size:28px;font-weight:500;color:var(--orange);letter-spacing:.5px}
.brand-mark{width:22px;height:22px;background:var(--orange)}
.main-nav{position:absolute;left:495px;top:0;height:102px;display:flex;align-items:center}
.nav-item{display:flex;align-items:center;gap:8px;height:102px;padding:0 24px;font-size:12.5px;text-transform:uppercase;color:#555;border-left:1px solid #e6e6e6}
.nav-item:first-child{border-left:0}
.nav-item svg{width:16px;height:16px;fill:var(--accent)}
.login-btn{position:absolute;left:1035px;top:40px;width:77px;height:31px;background:var(--orange);color:#fff;font-size:13px;display:flex;align-items:center;justify-content:center;border-radius:3px;box-shadow:0 1px 2px rgba(0,0,0,.25)}

.hero{position:absolute;left:86px;top:120px;width:1030px;height:513px;border:2px solid #fff;box-shadow:0 14px 24px rgba(0,0,0,.25)}
.hero-photo{position:absolute;inset:0;background:linear-gradient(100deg,#9fb7c3 0%,#d9e3e7 35%,#8a8f96 60%,#c8d4da 100%)}
.hero-caption{position:absolute;left:24px;top:348px;width:452px;height:125px;background:rgba(42,159,192,.82);padding:18px 32px;font-family:"Oswald",Arial,sans-serif;color:#fff;font-size:38px;line-height:46px;text-transform:uppercase}
.hero-arrow{position:absolute;top:432px;width:34px;height:34px;border-radius:50%;background:rgba(90,90,90,.75);display:flex;align-items:center;justify-content:center}
.hero-arrow svg{width:14px;height:14px;stroke:#fff;stroke-width:2.5;fill:none}

.card{position:absolute;background:var(--white);box-shadow:0 1px 4px rgba(0,0,0,.2)}
.card-head{height:41px;background:var(--panel-head);padding:0 24px;display:flex;align-items:center;font-size:14px;text-transform:uppercase;color:#555}

.profile{left:89px;top:705px;width:339px;height:304px}
.profile-photo{position:absolute;left:20px;top:66px;width:109px;height:91px;background:linear-gradient(135deg,#c9a184,#6c5a4f)}
.profile-name{position:absolute;left:150px;top:82px;font-size:21px;color:#333}
.profile-role{position:absolute;left:150px;top:117px;font-size:15px;color:var(--accent-dark)}
.profile-address{position:absolute;left:24px;top:190px;display:flex;gap:12px;font-size:14.5px;line-height:20px;color:#444}
.profile-address small{display:block;font-size:14px;color:var(--muted)}
.profile-phone{position:absolute;left:0;top:245px;width:100%;border-top:1px solid var(--line);padding:10px 24px;display:flex;gap:12px;align-items:center;font-size:15px;color:var(--accent)}
.icon{width:12px;height:14px;fill:#666;flex:none}

.chats{left:89px;top:1027px;width:339px;height:348px}
.chat-row{height:97px;display:flex;align-items:center;padding-left:24px;border-bottom:1px solid var(--line)}
.chat-row:last-child{border-bottom:0}
.avatar{width:72px;height:72px;border-radius:50%;border:2px solid #ddd;flex:none}
.chat-text{margin-left:42px;font-size:15px;line-height:27px;color:#555}
.chat-text b{display:block;font-weight:500;color:var(--accent-dark)}

.notes{left:89px;top:1398px;width:339px;height:316px}
.notes-body{padding:18px 24px 0 24px;font-size:14.5px;line-height:24.5px;text-align:justify;color:#555}
.notes-body p+p{margin-top:10px}

.people{left:89px;top:1744px;width:335px;height:374px}
.people .card-head{height:38px;padding:0 12px;justify-content:space-between;font-size:16px;color:#222;text-transform:uppercase}
.people-grid{display:grid;grid-template-columns:repeat(3,105px);grid-auto-rows:105px;gap:4px;padding:4px 6px}
.person{background:linear-gradient(160deg,#e5ddd5,#a48a78)}

.post{left:456px;width:635px;height:454px}
.post-head{height:74px;display:flex;align-items:flex-start}
.post-badge{width:46px;height:46px;background:var(--accent)}
.post-meta{margin-left:18px;padding-top:6px;font-size:15px;line-height:24px;color:#777}
.post-meta a{color:var(--link)}
.post-photo{height:234px;margin:0 2px}
.post-body{position:relative;padding:14px 16px 0 16px;font-size:15px;line-height:19px;color:#777}
.post-body .event-name{color:var(--link)}
.join-btn{position:absolute;right:40px;top:20px;width:69px;height:27px;border:1px solid #999;border-radius:3px;display:flex;align-items:center;justify-content:center;gap:6px;font-size:13px;font-weight:700;color:#333;box-shadow:0 1px 2px rgba(0,0,0,.2)}
.join-btn svg{width:16px;height:13px}
.post-actions{margin-top:28px;font-size:15px;color:var(--link)}

.site-footer{position:absolute;left:0;top:2175px;width:1200px;height:231px;background:var(--footer)}
.footer-col{position:absolute;top:40px}
.footer-col h4{font-size:13.5px;font-weight:400;text-transform:uppercase;color:#333;margin-bottom:14px}
.footer-col li{list-style:none;font-size:11.5px;line-height:23.5px;color:#444}
.social{position:absolute;left:924px;top:52px;display:flex;gap:14px}
.social span{width:28px;height:28px;border-radius:50%;border:2px solid #fff;box-shadow:0 1px 2px rgba(0,0,0,.2)}
.lang{position:absolute;left:931px;top:140px}
.lang h4{font-size:13.5px;font-weight:400;color:#333;margin-bottom:14px}
.lang-select{width:182px;height:36px;background:#fff;display:flex;align-items:center;justify-content:space-between;padding:0 14px;font-size:11.5px;color:#333}
.footer-bar{position:absolute;left:0;top:2406px;width:1200px;height:67px;background:var(--footer-bar);color:#ddd;font-size:12px;display:flex;align-items:center;justify-content:center}
</style>
</head>
<body>

<header class="site-header">
  <div class="brand"><span class="brand-mark"></span>TEAMORA</div>
  <nav class="main-nav">
    <a class="nav-item"><svg viewBox="0 0 16 16"><path d="M8 2 1 8h2v6h4v-4h2v4h4V8h2z"/></svg></a>
    <a class="nav-item"><svg viewBox="0 0 16 16"><path d="M1 3h14v10H1zm1.5 1.5v.3L8 9l5.5-4.2v-.3zM2.5 6.6v4.9h11V6.6L8 10.8z"/></svg>Messages</a>
    <a class="nav-item"><svg viewBox="0 0 16 16"><circle cx="5" cy="5" r="2.5"/><circle cx="11" cy="5" r="2.5"/><path d="M0 13c0-3 2-5 5-5s5 2 5 5zM8 13c.5-3 1.5-5 3-5 3 0 5 2 5 5z"/></svg>People</a>
    <a class="nav-item"><svg viewBox="0 0 16 16"><ellipse cx="6" cy="6" rx="6" ry="4.5"/><ellipse cx="11" cy="10" rx="5" ry="3.5"/></svg>Groups</a>
    <a class="nav-item"><svg viewBox="0 0 16 16"><path d="M1 3h14v12H1zm1.5 4v6.5h11V7zM4 1h2v3H4zm6 0h2v3h-2z"/></svg>Events</a>
  </nav>
  <a class="login-btn">LOGIN</a>
</header>

<section class="hero">
  <div class="hero-photo" role="img" aria-label="Photo of colleagues talking around a table in a bright office"></div>
  <div class="hero-caption">Social Media Platform<br>Teamora</div>
  <span class="hero-arrow" style="left:926px"><svg viewBox="0 0 14 14"><path d="M9 2 4 7l5 5"/></svg></span>
  <span class="hero-arrow" style="left:969px"><svg viewBox="0 0 14 14"><path d="M5 2l5 5-5 5"/></svg></span>
</section>

<aside>
  <div class="card profile">
    <div class="card-head">Profile</div>
    <div class="profile-photo" role="img" aria-label="Profile photo of the user"></div>
    <div class="profile-name">John Doe’s</div>
    <div class="profile-role">Account Manager</div>
    <div class="profile-address">
      <svg class="icon" viewBox="0 0 12 14"><path d="M6 0a4.5 4.5 0 0 0-4.5 4.5C1.5 8 6 14 6 14s4.5-6 4.5-9.5A4.5 4.5 0 0 0 6 0zm0 6.3a1.8 1.8 0 1 1 0-3.6 1.8 1.8 0 0 1 0 3.6z"/></svg>
      <div>Your Adress<small>City, Country</small></div>
    </div>
    <div class="profile-phone">
      <svg class="icon" viewBox="0 0 12 14"><path d="M2.5 1 5 3.5 3.8 5.2c.8 1.8 2 3.1 3.8 4L9 8l2.5 2.5-1.8 2C5 12 1 8 .8 3z"/></svg>
      Add phone number
    </div>
  </div>

  <div class="card chats">
    <div class="card-head">Chats</div>
    <div class="chat-row"><div class="avatar" role="img" aria-label="Contact portrait" style="background:linear-gradient(#b98a6c,#6e4a37)"></div><div class="chat-text">Account Manager<b>September 16, 2015</b></div></div>
    <div class="chat-row"><div class="avatar" role="img" aria-label="Contact portrait" style="background:linear-gradient(#d9cfc6,#5b4b40)"></div><div class="chat-text">Account Manager<b>September 16, 2015</b></div></div>
    <div class="chat-row"><div class="avatar" role="img" aria-label="Contact portrait" style="background:linear-gradient(#f0e6dc,#c7a889)"></div><div class="chat-text">Account Manager<b>September 16, 2015</b></div></div>
  </div>

  <div class="card notes">
    <div class="card-head">Notifications</div>
    <div class="notes-body">
      <p>Lorem Ipsum has been the industry's standard dummy text ever since the 1500s, when an unknown printer took a galley of type and scrambled it to make a type specimen book.</p>
      <p>It has survived not only five centuries, but also the leap into electronic typesetting, remaining essentially unchanged. It was popularised in the 1960s with the release</p>
    </div>
  </div>

  <div class="card people">
    <div class="card-head">People List<svg width="10" height="14" viewBox="0 0 10 14"><path d="M2 2l5 5-5 5" stroke="#555" stroke-width="2.5" fill="none"/></svg></div>
    <div class="people-grid">
      <div class="person" role="img" aria-label="Member portrait"></div>
      <div class="person" role="img" aria-label="Member portrait" style="background:linear-gradient(160deg,#eeeeee,#8a7a70)"></div>
      <div class="person" role="img" aria-label="Member portrait" style="background:linear-gradient(160deg,#f2ece6,#6b4a36)"></div>
      <div class="person" role="img" aria-label="Member portrait" style="background:linear-gradient(160deg,#bfc5c9,#3aa6c8)"></div>
      <div class="person" role="img" aria-label="Member portrait" style="background:linear-gradient(160deg,#f0f0f0,#a58c79)"></div>
      <div class="person" role="img" aria-label="Member portrait" style="background:linear-gradient(160deg,#efe6de,#5e3a2a)"></div>
      <div class="person" role="img" aria-label="Member portrait" style="background:linear-gradient(160deg,#e8e8e8,#2b2b2b)"></div>
    </div>
  </div>
</aside>

<main>
  <article class="card post" style="top:712px">
    <div class="post-head"><span class="post-badge"></span><div class="post-meta"><a>Teamora</a> created an event.<br>september 2, 2013</div></div>
    <div class="post-photo" role="img" aria-label="Photo of a conference hall with microphones and glasses on a table" style="background:linear-gradient(180deg,#7c6a66 0%,#b59a8f 45%,#e9e5e0 75%,#cfc6bd 100%)"></div>
    <div class="post-body">
      <div class="event-name">Event name</div>
      Tuesday, September 3, 2013 at 6:00pm<br>Adress, City, Country, 1051
      <span class="join-btn"><svg viewBox="0 0 16 13"><rect x="1" y="1" width="14" height="11" fill="none" stroke="#2a5fa0" stroke-width="1.5"/><rect x="1" y="1" width="14" height="3" fill="#2a5fa0"/></svg>Join</span>
      <div class="post-actions">Like · Comment · Get Notifications · Share</div>
    </div>
  </article>

  <article class="card post" style="top:1187px">
    <div class="post-head"><span class="post-badge"></span><div class="post-meta"><a>Teamora</a> created an event.<br>september 3, 2013</div></div>
    <div class="post-photo" role="img" aria-label="Photo of friends laughing together at an outdoor cafe" style="background:linear-gradient(90deg,#5d6a55 0%,#c9b27a 30%,#2d2a30 55%,#a37a5a 80%,#d8d0c2 100%)"></div>
    <div class="post-body">
      <div class="event-name">Event name</div>
      Tuesday, September 3, 2013 at 6:00pm<br>Adress, City, Country, 1051
      <span class="join-btn"><svg viewBox="0 0 16 13"><rect x="1" y="1" width="14" height="11" fill="none" stroke="#2a5fa0" stroke-width="1.5"/><rect x="1" y="1" width="14" height="3" fill="#2a5fa0"/></svg>Join</span>
      <div class="post-actions">Like · Comment · Get Notifications · Share</div>
    </div>
  </article>

  <article class="card post" style="top:1663px">
    <div class="post-head"><span class="post-badge"></span><div class="post-meta"><a>Teamora</a> created an event.<br>september 3, 2013</div></div>
    <div class="post-photo" role="img" aria-label="Photo of a speaker addressing a large audience" style="background:linear-gradient(90deg,#1c2440 0%,#2f3a6a 35%,#b0603c 60%,#d9a070 100%)"></div>
    <div class="post-body">
      <div class="event-name">Event name</div>
      Tuesday, September 3, 2013 at 6:00pm<br>Adress, City, Country, 1051
      <span class="join-btn"><svg viewBox="0 0 16 13"><rect x="1" y="1" width="14" height="11" fill="none" stroke="#2a5fa0" stroke-width="1.5"/><rect x="1" y="1" width="14" height="3" fill="#2a5fa0"/></svg>Join</span>
      <div class="post-actions">Like · Comment · Get Notifications · Share</div>
    </div>
  </article>
</main>

<footer class="site-footer">
  <div class="footer-col" style="left:91px"><h4>About</h4><ul><li>About PalNet</li><li>Advertising</li><li>Blog</li><li>Donate</li><li>Feedback</li><li>Jobs</li></ul></div>
  <div class="footer-col" style="left:277px"><h4>Help</h4><ul><li>FAQ</li><li>Help Forum</li><li>Contact Us</li><li>Terms of Service</li><li>Privacy Policy</li></ul></div>
  <div class="footer-col" style="left:485px"><h4>Make New Friends</h4><ul><li>Search &amp; Meet People</li><li>Who's Online Now?</li><li>Language Exchange</li><li>Play Matches</li><li>Live Global Updates</li><li>Invite Friends</li></ul></div>
  <div class="footer-col" style="left:730px"><h4>Your Profile</h4><ul><li>Profile Page</li><li>Upload Photos</li><li>Who viewed me</li><li>Messages</li><li>Friends</li><li>Bookmarks</li></ul></div>
  <div class="social"><span style="background:#3b5b97"></span><span style="background:#2aa3e0"></span><span style="background:#d9473a"></span><span style="background:#1f86bd"></span></div>
  <div class="lang"><h4>WEBSITE LANGUAGE</h4><div class="lang-select">English<svg width="8" height="6" viewBox="0 0 8 6"><path d="M1 1l3 3 3-3" stroke="#666" stroke-width="1.3" fill="none"/></svg></div></div>
</footer>
<div class="footer-bar">© 2015 . Terms of Service | Privacy Policy</div>

</body>
</html>
```